Letterhead, stationery and email signature for construction business

I need the letterhead, stationery and email signature designs for a construction business. I want them to have a corporate feel to them.

I've attached the logo for reference.

```html
<!DOCTYPE html>
<html lang="en">
<head>
<meta charset="utf-8">
<title>Halvern Works – Business Card</title>
<link rel="stylesheet" href="https://fonts.googleapis.com/css2?family=Montserrat:wght@700&family=Roboto:wght@300;400&display=swap">
<style>
  :root {
    --brand-blue: #2d57a5;
    --ink-grey: #55555c;
    --card-white: #ffffff;
    --backdrop: #1e1f22;
  }
  * { margin: 0; padding: 0; box-sizing: border-box; }
  html, body { width: 1200px; height: 800px; overflow: hidden; background: var(--backdrop); }
  .canvas {
    width: 1200px; height: 800px;
    display: flex; align-items: center; justify-content: center; gap: 60px;
  }
  .card {
    width: 525px; height: 300px; position: relative; flex: none;
    box-shadow: 0 10px 30px rgba(0,0,0,.5);
  }
  .card--front { background: var(--card-white); }
  .card--back { background: var(--brand-blue); display: flex; align-items: center; justify-content: center; }

  .wordmark {
    display: flex; align-items: center; gap: 12px;
    font-family: 'Montserrat', sans-serif; font-weight: 700;
    font-size: 34px; letter-spacing: 1px; line-height: 1; white-space: nowrap;
  }
  .wordmark__square { width: 30px; height: 30px; flex: none; }
  .card--front .wordmark { color: var(--brand-blue); position: absolute; top: 52px; left: 0; right: 0; justify-content: center; }
  .card--front .wordmark__square { background: var(--brand-blue); }
  .card--back .wordmark { color: var(--card-white); }
  .card--back .wordmark__square { background: var(--card-white); }

  .identity {
    position: absolute; top: 148px; right: 283px; text-align: right; white-space: nowrap;
  }
  .identity__name {
    font-family: 'Montserrat', sans-serif; font-weight: 700;
    font-size: 18px; color: var(--brand-blue); text-transform: uppercase;
  }
  .identity__role {
    font-family: 'Roboto', sans-serif; font-weight: 300;
    font-size: 16px; color: var(--ink-grey); margin-top: 2px;
  }
  .divider {
    position: absolute; left: 262px; top: 142px; width: 1px; height: 70px;
    background: var(--ink-grey);
  }
  .contact-list {
    position: absolute; left: 280px; top: 141px; list-style: none;
    font-family: 'Roboto', sans-serif; font-size: 16px; color: var(--ink-grey);
  }
  .contact-list li, .address {
    display: flex; align-items: center; gap: 8px; height: 24px; white-space: nowrap;
  }
  .icon { width: 14px; height: 14px; flex: none; fill: var(--brand-blue); }
  .address {
    position: absolute; left: 70px; top: 238px;
    font-family: 'Roboto', sans-serif; font-size: 16px; color: var(--ink-grey);
  }
</style>
</head>
<body>
<main class="canvas">
  <section class="card card--front">
    <div class="wordmark"><span class="wordmark__square"></span>HALVERN WORKS</div>

    <div class="identity">
      <p class="identity__name">Daniel R. Ostrand</p>
      <p class="identity__role">Founder &amp; CEO</p>
    </div>
    <span class="divider"></span>
    <ul class="contact-list">
      <li>
        <svg class="icon" viewBox="0 0 24 24"><path d="M6.6 10.8a15.1 15.1 0 0 0 6.6 6.6l2.2-2.2a1 1 0 0 1 1-.25 11.4 11.4 0 0 0 3.6.57 1 1 0 0 1 1 1V20a1 1 0 0 1-1 1A17 17 0 0 1 3 4a1 1 0 0 1 1-1h3.5a1 1 0 0 1 1 1c0 1.25.2 2.450.57 3.57a1 1 0 0 1-.25 1z"/></svg>
        (555)210-0147
      </li>
      <li>
        <svg class="icon" viewBox="0 0 24 24"><path d="M2 5h20v14H2zm2 2v.4l8 5.3 8-5.3V7zm0 2.8V17h16V9.8l-8 5.3z"/></svg>
        info@halvernworks.com
      </li>
      <li>
        <svg class="icon" viewBox="0 0 24 24"><path d="M12 2a10 10 0 1 0 0 20 10 10 0 0 0 0-20zm6.9 6h-3a15 15 0 0 0-1.3-3.9A8 8 0 0 1 18.9 8zM12 4c.8 1.1 1.5 2.5 1.9 4h-3.8c.4-1.5 1.1-2.9 1.9-4zM4.3 14a8 8 0 0 1 0-4h3.4a16 16 0 0 0 0 4zm.8 2h3a15 15 0 0 0 1.3 3.9A8 8 0 0 1 5.1 16zm3-8h-3a8 8 0 0 1 4.3-3.9A15 15 0 0 0 8.1 8zM12 20c-.8-1.1-1.5-2.5-1.9-4h3.8c-.4 1.5-1.1 2.9-1.9 4zm2.3-6H9.7a14 14 0 0 1 0-4h4.6a14 14 0 0 1 0 4zm.3 5.9a15 15 0 0 0 1.3-3.9h3a8 8 0 0 1-4.3 3.9zm1.7-5.9a16 16 0 0 0 0-4h3.4a8 8 0 0 1 0 4z"/></svg>
        www.halvernworks.com
      </li>
    </ul>
    <p class="address">
      <svg class="icon" viewBox="0 0 24 24"><path d="M12 2a7 7 0 0 0-7 7c0 5.2 7 13 7 13s7-7.8 7-13a7 7 0 0 0-7-7zm0 9.5A2.5 2.5 0 1 1 12 6.5a2.5 2.5 0 0 1 0 5z"/></svg>
      4420 Harbor Point Drive, Brookvale, CA 90417
    </p>
  </section>

  <section class="card card--back">
    <div class="wordmark"><span class="wordmark__square"></span>HALVERN WORKS</div>
  </section>
</main>
</body>
</html>
```